TAVILN soap beauty bar

I need a box designed to put a 4oz bar of soap inside. All sides of the box need design. A refreshingly fragrant blend of citrus and spicy notes, it is made with a blend of essential oils including ginger, mandarin, lemon and orange flowers

Target Market(s)

Homeless people

Requirements
Must have
• My company logo as pictured with text and design like a standard bar of soap. Weight 4oz, ingredients:
Olive oil, Coconut oil,Organic sustainable palm oil,Water,Lye,Shea butter, orange, ginger, mandarin, lemon essential oil. uploading pics for inspiration.
Nice to have
• The soap box measurements are Dimensions (L x W x H). 5.75 x 3.80 x 5.60 Inches ...

```html
<!DOCTYPE html>
<html lang="en">
<head>
<meta charset="utf-8">
<title>TAVILN soap beauty bar box dieline</title>
<link rel="stylesheet" href="https://fonts.googleapis.com/css2?family=Exo+2:wght@600&family=Montserrat:wght@500;700;800&display=swap">
<style>
  :root {
    --bg: #e4e5ea;
    --green: #3a982a;
    --green-deep: #2f8a24;
    --green-light: #b9df8c;
    --white: #ffffff;
    --line: #5b5b5b;
    --mark-red: #d8322c;
  }
  html, body {
    margin: 0;
    width: 1200px;
    height: 890px;
    overflow: hidden;
    background: var(--bg);
  }
  .dieline {
    display: block;
    width: 1200px;
    height: 890px;
  }
  .panel-green { fill: var(--green); }
  .panel-white { fill: var(--white); stroke: var(--line); stroke-width: 1; }
  .brand-name {
    font-family: "Montserrat", sans-serif;
    font-weight: 800;
    fill: var(--green-deep);
  }
  .product-title {
    font-family: "Exo 2", sans-serif;
    font-weight: 600;
    fill: var(--white);
  }
  .info-heading {
    font-family: "Montserrat", sans-serif;
    font-weight: 700;
    font-size: 8.5px;
    fill: var(--white);
  }
  .info-text {
    font-family: "Montserrat", sans-serif;
    font-weight: 500;
    font-size: 7px;
    fill: var(--white);
  }
  .brand-dot { fill: var(--mark-red); }
</style>
</head>
<body>
<svg class="dieline" viewBox="595 865 1020 757" xmlns="http://www.w3.org/2000/svg" aria-label="Flat box dieline for TAVILN soap beauty bar">
  <defs>
    <linearGradient id="fade-white-green" x1="0" x2="1" y1="0" y2="0">
      <stop offset="0" stop-color="#ffffff"/>
      <stop offset="1" stop-color="#b9df8c"/>
    </linearGradient>
    <linearGradient id="fade-green-white" x1="0" x2="1" y1="0" y2="0">
      <stop offset="0" stop-color="#b9df8c"/>
      <stop offset="1" stop-color="#ffffff"/>
    </linearGradient>
  </defs>

  <!-- back panel with dust flaps -->
  <g class="back-panel" role="img" aria-label="Green panel with fine scattered line pattern">
    <polygon class="panel-green"
      points="725,880 897,880 897,905 947,990 947,1550 897,1600 897,1620 725,1620 725,1600 665,1560 665,1475 608,1445 608,1050 665,1020 665,935"/>
  </g>
  <g class="back-info">
    <g transform="rotate(-90 700 1410)">
      <text class="info-heading" x="700" y="1410">TAVILN SOAP</text>
      <text class="info-heading" x="700" y="1421">BEAUTY BAR · NET WT 4 OZ</text>
      <text class="info-text" x="700" y="1432">A refreshing blend of citrus and spicy</text>
      <text class="info-text" x="700" y="1441">notes with ginger, mandarin, lemon</text>
      <text class="info-text" x="700" y="1450">and orange flower essential oils.</text>
      <text class="info-heading" x="700" y="1475">DIRECTIONS</text>
      <text class="info-text" x="700" y="1485">Wet the bar, lather in hands and</text>
      <text class="info-text" x="700" y="1494">apply gently. Rinse well with water.</text>
      <text class="info-text" x="700" y="1503">Store in a dry place.</text>
      <text class="info-text" x="700" y="1535">Olive oil</text>
      <text class="info-text" x="700" y="1544">Coconut oil</text>
      <text class="info-text" x="700" y="1553">Shea butter</text>
      <text class="info-text" x="700" y="1562">Palm oil</text>
      <text class="info-text" x="700" y="1571">Lemon oil</text>
      <text class="info-text" x="760" y="1535">Ingredients: olive oil, coconut oil,</text>
      <text class="info-text" x="760" y="1544">organic sustainable palm oil, water, lye,</text>
      <text class="info-text" x="760" y="1553">shea butter, orange, ginger, mandarin,</text>
      <text class="info-text" x="760" y="1562">lemon essential oil.</text>
    </g>
  </g>

  <!-- side panel one -->
  <g class="side-panel-left">
    <polygon class="panel-green" points="985,910 1105,910 1133,1000 1133,1030 958,1030 958,1000"/>
    <rect x="958" y="1030" width="175" height="440" fill="url(#fade-white-green)" stroke="#5b5b5b" stroke-width="0.6"/>
    <polygon class="panel-green" points="958,1470 1133,1470 1133,1500 1105,1590 985,1590 958,1500"/>
    <text class="brand-name" font-size="58" text-anchor="middle" transform="rotate(-90 1066 1250)" x="1066" y="1250">TAVILN</text>
  </g>

  <!-- front panel with tuck flaps -->
  <g class="front-panel">
    <polygon class="panel-white" points="1185,880 1370,880 1385,915 1410,915 1410,1030 1133,1030 1133,1000 1145,915 1170,915"/>
    <rect x="1133" y="1030" width="267" height="440" fill="url(#fade-green-white)" stroke="#5b5b5b" stroke-width="0.6"/>
    <polygon class="panel-white" points="1133,1470 1410,1470 1410,1615 1143,1615 1143,1500 1133,1500"/>
    <circle class="brand-dot" cx="1188" cy="1250" r="17"/>
    <text class="brand-name" font-size="26" text-anchor="middle" transform="rotate(-90 1250 1250)" x="1250" y="1250">TAVILN</text>
    <g class="title-band" role="img" aria-label="Green band with fine scattered line pattern">
      <rect class="panel-green" x="1273" y="985" width="127" height="535"/>
    </g>
    <g transform="rotate(-90 1336 1255)">
      <text class="product-title" font-size="35" text-anchor="middle" x="1336" y="1240">Citrus soap</text>
      <text class="product-title" font-size="35" text-anchor="middle" x="1336" y="1275">beauty bar 4 oz</text>
    </g>
  </g>

  <!-- glue strip -->
  <rect x="1400" y="1030" width="22" height="440" fill="#c9e6a6" stroke="#5b5b5b" stroke-width="0.6"/>

  <!-- side panel two -->
  <g class="side-panel-right">
    <polygon class="panel-green" points="1455,910 1597,910 1597,1030 1422,1030 1422,1000"/>
    <rect x="1422" y="1030" width="175" height="440" fill="url(#fade-green-white)" stroke="#5b5b5b" stroke-width="0.6"/>
    <polygon class="panel-green" points="1422,1470 1597,1470 1597,1590 1455,1590 1422,1500"/>
    <circle class="brand-dot" cx="1490" cy="1250" r="17"/>
    <text class="brand-name" font-size="26" text-anchor="middle" transform="rotate(-90 1545 1250)" x="1545" y="1250">TAVILN</text>
  </g>
</svg>
</body>
</html>
```